Website redesign - vorelmik.com

We are looking to do a full redesign of vorelmik.com. Need a designer to come up overall layout and 3 specific pages and 3 different hero images.
Wireframes for the 3 pages are attached as well as site images. You don't have to follow the wireframes exactly, but instead the wireframe is there to show you the information that needs to be on each page. Feel free to rearrange as needed.
Our target market is self taught engineers. So definitely I want a more casual feel to it. I'm ok with fun bold colors as well. Really like websites that have the infinite scroll look/feel to them.
Looking to find a designer who will produce HTML and potentially even implement the HTML into our site checked in code.
HTML Code should be responsive/mobile first leveraging Bootstrap 4.
Attached files include:
0) Wireframe PDF
https://files.plomwerk.net/d/7Kx2pQmW9zLr4TbN8vYc3HsE5fJ/view?mode=share
1) Vorelmik Images zip 1
https://files.plomwerk.net/d/4Gt8nRvB2wQx6MkZ1pLd9YaC7hU/view?mode=share
2) Vorelmik Images zip 2
https://files.plomwerk.net/d/9Jw3sTcF5yNv1HqX8rKb2ZeM6dP/view?mode=share
Target Market(s)
I sell DIY Waterproof Electronics enclosures. Target audience is self taught DIY engineers
Coding
Coded - Design and coding required
Number of Pages Required
3 page
Colors
Designer to choose colors to be used in the design.
Look and feel

```html
<!DOCTYPE html>
<html lang="en">
<head>
<meta charset="utf-8">
<title>Vorelmik – Waterproof Project Boxes</title>
<link rel="stylesheet" href="https://fonts.googleapis.com/css2?family=Audiowide&family=Lato:wght@400;700&display=swap">
<style>
:root{
  --blue:#0a0af5;
  --lime:#cdd200;
  --ink:#333333;
  --muted:#555555;
  --line:#cfcfcf;
  --footer:#3a3a3a;
  --white:#ffffff;
}
*{box-sizing:border-box;margin:0;padding:0}
html,body{width:1200px;height:4304px;overflow:hidden;background:var(--white)}
body{position:relative;font-family:'Lato',sans-serif;color:var(--ink)}
.btn{position:absolute;display:flex;align-items:center;justify-content:center;border-radius:30px;background:var(--lime);color:#333;font-size:14px;text-decoration:none}
.btn-outline{background:var(--white);border:2px solid var(--lime)}

/* header */
.site-header{position:absolute;left:0;top:0;width:1200px;height:92px;background:var(--white)}
.brand{position:absolute;left:125px;top:24px;display:flex;align-items:center;gap:10px;font-family:'Audiowide',sans-serif;font-size:36px;color:var(--blue)}
.brand-dot{width:14px;height:14px;border-radius:50%;background:var(--lime)}
.main-nav a{position:absolute;top:38px;font-size:13px;color:#444;text-decoration:none}

/* hero */
.hero{position:absolute;left:0;top:92px;width:1200px;height:730px}
.hero-photo{position:absolute;inset:0 0 90px 0;background:linear-gradient(120deg,#6b5a47 0%,#8d7a62 30%,#2b2b2b 55%,#a9a294 75%,#8a8478 100%)}
.hero-curve{position:absolute;left:0;bottom:0;width:1200px;height:180px}
.hero-kicker{position:absolute;left:0;width:1200px;top:252px;text-align:center;font-family:'Audiowide',sans-serif;font-size:27px;color:#fff}
.hero-title{position:absolute;left:0;width:1200px;top:280px;text-align:center;font-family:'Audiowide',sans-serif;font-size:40px;color:#fff}
.hero-note{position:absolute;left:0;width:1200px;top:346px;text-align:center;font-size:13px;color:#fff}

/* features */
.media{position:absolute}
.frame-line{position:absolute;background:var(--lime)}
.block{position:absolute;background:var(--blue)}
.feature-title{position:absolute;font-family:'Audiowide',sans-serif;font-size:27px;line-height:34px;color:var(--blue);font-weight:400}
.feature-text{position:absolute;font-size:13.5px;line-height:24px;color:var(--muted)}
.feature-list{position:absolute;list-style:none;font-size:13.5px;line-height:28px;color:var(--muted)}
.feature-list li{position:relative;padding-left:20px}
.feature-list li::before{content:"";position:absolute;left:0;top:12px;width:5px;height:5px;border-radius:50%;background:var(--lime)}

/* testimonials */
.section-title{position:absolute;left:0;width:1200px;text-align:center;font-family:'Audiowide',sans-serif;font-size:27px;color:var(--blue);font-weight:400}
.quote-card{position:absolute;border:2px solid var(--line);border-radius:0 38px 0 0;background:var(--white)}
.quote-mark{position:absolute;left:70px;top:18px;font-family:'Audiowide',sans-serif;font-size:42px;color:var(--lime)}
.quote-text{position:absolute;left:68px;top:62px;width:292px;font-size:13px;line-height:24px;color:var(--muted)}
.quote-name{position:absolute;right:38px;bottom:22px;font-family:'Audiowide',sans-serif;font-size:18px;color:var(--blue)}
.avatar{position:absolute;width:90px;height:90px;border-radius:50%;background:linear-gradient(#d8d8d8,#9a9a9a);border:4px solid #fff;box-shadow:0 2px 6px rgba(0,0,0,.25)}

/* gallery */
.build{position:absolute;width:306px}
.build-photo{width:306px;height:219px;border:1px solid var(--line);background:radial-gradient(circle at 50% 50%,#5f6b5a 0%,#3a3a3a 35%,#f3f3f3 70%)}
.build-name{margin-top:16px;text-align:center;font-size:12px;color:#555}

/* footer */
.bulb-mark{position:absolute;left:583px;top:4205px;width:34px;height:34px;border-radius:50%;background:var(--lime)}
.site-footer{position:absolute;left:0;top:4264px;width:1200px;height:40px;background:var(--footer);color:#fff;font-size:13px}
.site-footer .copy{position:absolute;left:120px;top:12px}
.site-footer .follow{position:absolute;left:945px;top:12px}
.social{position:absolute;top:9px;width:22px;height:22px;border-radius:50%;border:1.5px solid #fff}
</style>
</head>
<body>

<header class="site-header">
  <div class="brand"><span>Vorelmik</span><span class="brand-dot"></span></div>
  <nav class="main-nav">
    <a href="#" style="left:403px">Get started</a>
    <a href="#" style="left:506px">Designs</a>
    <a href="#" style="left:590px">FAQs</a>
    <a href="#" style="left:660px">Videos</a>
    <a href="#" style="left:737px">Contact us</a>
  </nav>
  <a href="#" class="btn btn-outline" style="left:850px;top:31px;width:114px;height:33px">Sign in</a>
  <a href="#" class="btn" style="left:971px;top:31px;width:112px;height:33px">Sign Up</a>
</header>

<section class="hero">
  <div class="hero-photo" role="img" aria-label="Grey and black waterproof project boxes mounted outdoors against a brick wall with cables"></div>
  <svg class="hero-curve" viewBox="0 0 1200 180" preserveAspectRatio="none">
    <path d="M0 60 Q600 -40 1200 60 L1200 180 L0 180 Z" fill="#ffffff"/>
    <path d="M0 150 Q300 70 620 60 Q420 75 0 130 Z" fill="#0a0af5"/>
    <path d="M690 62 Q1000 65 1200 100 L1200 128 Q1000 80 690 62 Z" fill="#cdd200"/>
  </svg>
  <div class="hero-kicker">Waterproof Project Boxes</div>
  <div class="hero-title">Customized to your Exact Needs.</div>
  <div class="hero-note">(at a fraction of the price)</div>
  <a href="#" class="btn" style="left:520px;top:383px;width:163px;height:45px">Get Started</a>
</section>

<!-- designer feature -->
<div class="media" style="left:0;top:902px;width:598px;height:426px;background:linear-gradient(#ececec,#d9d9d9)" role="img" aria-label="Video preview of the online box designer showing enclosure layout examples"></div>
<div class="frame-line" style="left:598px;top:1035px;width:64px;height:3px"></div>
<div class="frame-line" style="left:659px;top:1035px;width:3px;height:290px"></div>
<div class="frame-line" style="left:241px;top:1328px;width:3px;height:128px"></div>
<div class="frame-line" style="left:241px;top:1454px;width:357px;height:3px"></div>
<div class="block" style="left:600px;top:1327px;width:239px;height:236px"></div>
<h2 class="feature-title" style="left:702px;top:985px;width:380px">Customize your Project Box using our Designer</h2>
<p class="feature-text" style="left:702px;top:1075px;width:380px">Lorem Ipsum is simply dummy text of the printing and typesetting industry. Lorem Ipsum has been the industry's standard dummy text ever since the 1500s</p>
<a href="#" class="btn" style="left:709px;top:1195px;width:163px;height:45px">Get Started</a>

<!-- mounting kits -->
<div class="media" style="left:600px;top:1563px;width:600px;height:442px;background:linear-gradient(135deg,#d8d8d8,#3c4a3a 45%,#1e1e1e 70%,#bcbcbc)" role="img" aria-label="Open enclosure with green circuit boards and wiring mounted inside"></div>
<h2 class="feature-title" style="left:124px;top:1600px;width:450px">Mounting Kits for all the popular water proof project boxes with many sizes to choose from</h2>
<p class="feature-text" style="left:124px;top:1772px;width:380px">Lorem Ipsum is simply dummy text of the printing and typesetting industry. Lorem Ipsum has been the industry's standard dummy text ever since the 1500s</p>
<a href="#" class="btn" style="left:124px;top:1890px;width:163px;height:45px">Get Started</a>

<!-- makers -->
<div class="block" style="left:451px;top:2005px;width:147px;height:147px"></div>
<div class="frame-line" style="left:354px;top:2116px;width:3px;height:36px"></div>
<div class="frame-line" style="left:354px;top:2116px;width:97px;height:3px"></div>
<div class="frame-line" style="left:598px;top:2116px;width:70px;height:3px"></div>
<div class="frame-line" style="left:665px;top:2116px;width:3px;height:310px"></div>
<div class="media" style="left:0;top:2152px;width:598px;height:428px;background:linear-gradient(150deg,#c8c2b8,#e6e6e6 40%,#b9b3a6 80%)" role="img" aria-label="Shipping envelopes and bagged mounting kit hardware on a workbench"></div>
<h2 class="feature-title" style="left:702px;top:2140px;width:400px">Vorelmik waterproof project boxes were built by makers for makers</h2>
<ul class="feature-list" style="left:702px;top:2268px;width:420px">
  <li>Design to your specifications</li>
  <li>Maker components: Nordino, Bramble Pi, Velwatt Power</li>
  <li>Detailed build instructions, videos, walkthroughs</li>
  <li>DIY made to look professional</li>
</ul>
<a href="#" class="btn" style="left:702px;top:2410px;width:164px;height:45px">Get Started</a>

<!-- testimonials -->
<h2 class="section-title" style="top:2736px">What our Customers Have to Say</h2>
<div class="quote-card" style="left:179px;top:2837px;width:411px;height:178px">
  <div class="quote-mark">"</div>
  <p class="quote-text">Great work at a reasonable cost. I can't recom mend them enough. If you're doing custom boxes for light shows, this is where you go.</p>
  <div class="quote-name">Marta K</div>
</div>
<div class="avatar" style="left:120px;top:2879px" role="img" aria-label="Customer portrait"></div>
<div class="quote-card" style="left:668px;top:2837px;width:412px;height:178px">
  <div class="quote-mark">"</div>
  <p class="quote-text">Fantastic service/product..whether you simply generate the design and do all of the fabrication yourself or simply order the kits.</p>
  <div class="quote-name">Tomas V.</div>
</div>
<div class="avatar" style="left:607px;top:2879px" role="img" aria-label="Customer portrait"></div>

<!-- gallery -->
<h2 class="section-title" style="top:3237px">See Real Examples from our Customers</h2>
<figure class="build" style="left:120px;top:3317px"><div class="build-photo" role="img" aria-label="Assembled mounting plate build with circuit boards"></div><figcaption class="build-name">kelbox32026_standalone_primary</figcaption></figure>
<figure class="build" style="left:444px;top:3317px"><div class="build-photo" role="img" aria-label="Assembled mounting plate build with circuit boards"></div><figcaption class="build-name">kelbox32022_standalone_primary</figcaption></figure>
<figure class="build" style="left:769px;top:3317px"><div class="build-photo" role="img" aria-label="Assembled mounting plate build with relays"></div><figcaption class="build-name">kelbox32016_standalone_primary</figcaption></figure>
<figure class="build" style="left:120px;top:3601px"><div class="build-photo" role="img" aria-label="Two-tier build with power supply"></div><figcaption class="build-name">kelbox32012_standalone_primary</figcaption></figure>
<figure class="build" style="left:444px;top:3601px"><div class="build-photo" role="img" aria-label="Two-tier build with power supply"></div><figcaption class="build-name">kelbox32010_standalone_primary</figcaption></figure>
<figure class="build" style="left:769px;top:3601px"><div class="build-photo" role="img" aria-label="Mounting plate with power supply unit"></div><figcaption class="build-name">vp1500_standalone_primary</figcaption></figure>
<figure class="build" style="left:120px;top:3885px"><div class="build-photo" role="img" aria-label="Two-tier build with board and supply"></div><figcaption class="build-name">vkm30_standalone_primary</figcaption></figure>
<figure class="build" style="left:444px;top:3885px"><div class="build-photo" role="img" aria-label="Two-tier build with controller board"></div><figcaption class="build-name">vrc4_standalone_primary</figcaption></figure>
<figure class="build" style="left:769px;top:3885px"><div class="build-photo" role="img" aria-label="Two-tier build with controller board"></div><figcaption class="build-name">vrc8_standalone_primary</figcaption></figure>

<div class="bulb-mark"></div>
<footer class="site-footer">
  <span class="copy">Copyright © 2020 Vorelmik Designer.</span>
  <span class="follow">Follow us:</span>
  <span class="social" style="left:1018px" role="img" aria-label="Social link"></span>
  <span class="social" style="left:1053px" role="img" aria-label="Video channel link"></span>
</footer>

</body>
</html>
```